Stationery Design Project

I need a stationary design for our company. we are based in Houston, TX and we are called Mira Vell Lending. And we are wanting to brand our MoneyMendPlus program, which includes our tax preparation and restoration, credit repair service. Although our business offers other programs, we are interested in mainly focusing on The MoneyMendPlus program. We are looking for way to brand our ourselves and I believe that a great stationery design will help in achieving this goal. Our logo design is blue and light blue. the slogan is orange.

Industry/Entity Type

Business

Requirements
Must have
• Address: 30871 Calloway Ln. B-22
Houston, TX 75419
Tel. 555-318-6207
Fax 555-294-7153
www.miravelllending.example
info@miravelllending.example
Our Slogan: Confidence, Renewed!

```html
<!DOCTYPE html>
<html lang="en">
<head>
<meta charset="utf-8">
<title>Mira Vell Lending – Business Card</title>
<link rel="stylesheet" href="https://fonts.googleapis.com/css2?family=Tinos:wght@400;700&display=swap">
<style>
  :root {
    --backdrop: #e9e4de;
    --card: #ffffff;
    --navy: #123e66;
    --sky: #4d8fd1;
    --ink: #1f1f1f;
    --rule: #c9c9c9;
    --orange: #f0902a;
    --edge: #b9b3ab;
  }
  * { box-sizing: border-box; margin: 0; padding: 0; }
  html, body { width: 1200px; height: 374px; overflow: hidden; }
  body {
    position: relative;
    background: var(--backdrop);
    font-family: "Tinos", "Times New Roman", serif;
    color: var(--ink);
  }
  .card {
    position: absolute;
    top: 33px;
    width: 544px;
    height: 310px;
    background: var(--card);
    border: 1px solid var(--edge);
    overflow: hidden;
  }
  .card--front { left: 40px; }
  .card--back { left: 621px; }

  .brand {
    position: absolute;
    left: 48px; top: 40px;
    width: 191px; height: 192px;
    display: flex; align-items: center; justify-content: center; gap: 10px;
  }
  .brand__square { width: 22px; height: 22px; background: var(--navy); flex: none; }
  .brand__name { font-size: 19px; color: var(--navy); white-space: nowrap; }

  .divider {
    position: absolute; left: 278px; top: 37px;
    width: 1px; height: 220px; background: var(--rule);
  }
  .details { position: absolute; left: 299px; top: 50px; font-size: 15px; line-height: 20px; }
  .address { margin-bottom: 21px; }
  .contact { list-style: none; }
  .contact li { display: flex; align-items: center; gap: 7px; height: 21.3px; }
  .contact svg { width: 12px; height: 12px; fill: var(--ink); flex: none; }
  .slogan {
    margin-top: 24px;
    color: var(--orange); font-weight: 700; font-size: 16px; letter-spacing: 1.4px;
  }
  .band { position: absolute; left: 0; bottom: 0; width: 544px; height: 18px; }

  .program {
    position: absolute; left: 0; top: 164px; width: 100%;
    text-align: center; font-size: 53px; color: var(--navy); letter-spacing: -0.3px;
  }
  .site {
    position: absolute; left: 0; top: 259px; width: 100%;
    text-align: center; font-size: 14.5px; color: var(--navy); letter-spacing: 2.9px;
  }
  .site b { font-weight: 700; }
</style>
</head>
<body>
  <section class="card card--front">
    <div class="brand">
      <span class="brand__square"></span>
      <span class="brand__name">Mira Vell Lending</span>
    </div>
    <div class="divider"></div>
    <div class="details">
      <p class="address">30871 Calloway Ln. B-22<br>Houston, TX 75419</p>
      <ul class="contact">
        <li><svg viewBox="0 0 12 12" aria-hidden="true"><path fill-rule="evenodd" d="M6 0a6 6 0 1 0 0 12A6 6 0 0 0 6 0zm0 1.2a4.8 4.8 0 1 1 0 9.6 4.8 4.8 0 0 1 0-9.6z"/><path d="M4 3l1.3 1.6-.7.8c.5 1 1 1.5 2 2l.8-.7L9 8l-1 1C5.5 8.5 3.5 6.5 3 4z"/></svg>555-318-6207</li>
        <li><svg viewBox="0 0 12 12" aria-hidden="true"><path d="M3 1h5v3H3zM1 4h10v5H1zm1 6h8v1H2z"/></svg>555-294-7153</li>
        <li><svg viewBox="0 0 12 12" aria-hidden="true"><path d="M0 2h12v8H0zm1 1v.4l5 3.3 5-3.3V3z" fill-rule="evenodd"/></svg>info@miravelllending.example</li>
        <li><svg viewBox="0 0 12 12" aria-hidden="true"><g fill="none" stroke="var(--ink)" stroke-width="1"><circle cx="6" cy="6" r="5.3"/><ellipse cx="6" cy="6" rx="2.3" ry="5.3"/><path d="M0.8 6h10.4M1.6 3.4h8.8M1.6 8.6h8.8"/></g></svg>www.miravelllending.example</li>
      </ul>
      <p class="slogan">Confidence, Renewed!</p>
    </div>
    <svg class="band" viewBox="0 0 544 18" preserveAspectRatio="none" aria-hidden="true">
      <polygon points="0,0 282,0 262,18 0,18" fill="var(--navy)"/>
      <polygon points="290,0 544,0 544,18 270,18" fill="var(--sky)"/>
    </svg>
  </section>

  <section class="card card--back">
    <p class="program">MoneyMendPlus</p>
    <p class="site">www.<b>miravelllending</b>.example</p>
  </section>
</body>
</html>
```